Clean Modern Skin Product branding/ label.

I need a label for a skincare line. The company is Dermaloft but product names will vary. A couple products to list are:
Sensitive Cleanser, Lumeno, Repair, Halo up, Mendora, Mendora Plus, Mendora Intense, Tavelo, Balance and Vivanto.

I would like the color scheme to be muted greens, grays, tourquise. The bottles are white, boston shaped with pumps, and ounces are 2, 4, 8, 16 ounces. When I choose the design, I can give you exact label sizes. Along with the ingredience already on the product label.

The look I desire is clean, minimal. A modern, organic look. Ideas that come to mind are a Veloraine,https://www.veloraine-example.com/product/2846/37204/3-step/step-2-exfoliate/clarifying-lotion-1 and the simplicity of Bo Tarn.

Both styles high light the name, in this case Dermaloft, and then the specific product.

My product is clean utilizing pure ingredients rather that a bunch fillers and binders. When I work with my clients I normally will say we need to "restore the balance" from over use of harsh products. That is why this lines works. It restores the skin to it's natural state. The process is simple, so I would like the label to reflect that simplicity.

Target Market(s)

Anyone with sensitive skin. So gender neutral

Industry/Entity Type

Skin Care Product

Font styles to use
Serif
Sans Serif
Decorative

Colors
acd037
33b8a4
fcfefd
85cae6
d3d3d3

Requirements
Must have
• Logo, name of product and color identity for cleanser, Active products, moisturizers
• I am thinking we could have one color for a cleanser and a space where I can put a sticker on which cleanser it is. Acne Cleasner, Sensitive Cleanser, and Cleanser.
Nice to have
• Not sure....suprise me. I would like the font to stay the same on the DERMALOFT, but you can change color, or color of leaf.
Should not have
• Too busy, too crowded or look like every other skincare line

```html
<!DOCTYPE html>
<html lang="en">
<head>
<meta charset="utf-8">
<title>Dermaloft — Sensitive Cleanser Label</title>
<link rel="stylesheet" href="https://fonts.googleapis.com/css2?family=Michroma&family=Roboto:wght@300;700&display=swap">
<style>
  :root {
    --backdrop: #a6dc48;
    --label-white: #fcfefd;
    --stroke-turquoise: #aeefe6;
    --brand-gray: #5b5f63;
    --product-blue: #3d6e82;
    --rule-blue: #4a7d92;
    --leaf-green: #8fe03a;
  }
  * { margin: 0; padding: 0; box-sizing: border-box; }
  html, body { width: 1200px; height: 1200px; overflow: hidden; }
  body { background: var(--backdrop); position: relative; }

  .label {
    position: absolute;
    left: 150px;
    top: 85px;
    width: 900px;
    height: 1030px;
    background: var(--label-white);
    box-shadow: 0 6px 18px rgba(0,0,0,0.18);
  }

  .brush-stroke {
    position: absolute;
    left: 54px;
    top: 88px;
    width: 788px;
    height: 238px;
    background: linear-gradient(180deg, var(--stroke-turquoise) 0%, #b9f2ea 60%, rgba(174,239,230,0.55) 100%);
    border-radius: 40px 120px 30px 90px / 60px 40px 80px 50px;
  }

  .brand-name {
    position: absolute;
    left: 0;
    top: 150px;
    width: 100%;
    text-align: center;
    font-family: "Michroma", sans-serif;
    font-size: 82px;
    line-height: 1;
    color: var(--brand-gray);
    letter-spacing: -1px;
  }

  .product-name {
    position: absolute;
    left: 188px;
    top: 341px;
    width: 525px;
    height: 75px;
    border-top: 2px solid var(--rule-blue);
    border-bottom: 2px solid var(--rule-blue);
    text-align: center;
    font-family: "Roboto", sans-serif;
    font-weight: 300;
    font-size: 60px;
    line-height: 72px;
    color: var(--product-blue);
  }

  .brand-dot {
    position: absolute;
    left: 395px;
    top: 780px;
    width: 110px;
    height: 110px;
    border-radius: 50%;
    background: var(--leaf-green);
  }

  .tagline {
    position: absolute;
    left: 0;
    top: 918px;
    width: 100%;
    text-align: center;
    font-family: "Roboto", sans-serif;
    font-weight: 700;
    font-size: 40px;
    line-height: 1;
    color: var(--leaf-green);
  }
</style>
</head>
<body>
  <main class="label">
    <div class="brush-stroke" role="img" aria-label="Soft turquoise painted brush stroke behind the brand name"></div>
    <h1 class="brand-name">dermaloft</h1>
    <h2 class="product-name">Sensitive Cleanser</h2>
    <div class="brand-dot" aria-hidden="true"></div>
    <p class="tagline">restore the balance</p>
  </main>
</body>
</html>
```